Online business manager needs a website

I need a website designed and then coded. I am an online business manager serving a number of different industries providing administrative support to existing small businesses and helping solo practitioners get their new business up and running.

I didn't have a logo formally designed but have been using the attached avatar and wouldn't mind something that incorporated that.

The business doesn't have an official name, so I've just been using my name Lena Morvath, Online Business Manager or Lena Morvath, OBM. I've attached two documents that I have made previously for an example of content.

I would prefer the final site be in Wordpress.

Requirements
Must have
• A way to contact me, testimonials, list of services

```html
<!DOCTYPE html>
<html lang="en">
<head>
<meta charset="utf-8">
<title>Lena Morvath — Online Business Manager</title>
<link rel="stylesheet" href="https://fonts.googleapis.com/css2?family=Mulish:wght@300;400;600;700;800&display=swap">
<style>
:root{
  --ink:#1d1d2b;
  --muted:#555566;
  --purple:#4a1a8e;
  --purple-deep:#2e0b6e;
  --purple-bright:#7a2fd0;
  --pink:#b03ee0;
  --hero-blue:#1b3fb4;
  --hero-navy:#0a1a66;
  --lavender:#e7defb;
  --teal:#1ec6d6;
  --green:#22c66e;
  --green-teal:#16b08c;
  --teal-dark:#118687;
  --gold:#f4c21a;
  --white:#ffffff;
  --black:#050505;
}
*{box-sizing:border-box;margin:0;padding:0}
html,body{width:1200px;height:5296px;overflow:hidden}
body{position:relative;font-family:"Mulish",sans-serif;color:var(--ink);background:var(--white)}
.abs{position:absolute}
ul{list-style:none}

/* Hero */
.hero{position:absolute;left:0;top:0;width:1200px;height:740px;overflow:hidden;
  background:radial-gradient(ellipse at 30% 40%,#2750d0 0%,var(--hero-blue) 40%,var(--hero-navy) 100%)}
.hero-wave{position:absolute;left:0;top:0}
.nav{position:absolute;left:68px;top:22px;width:1064px;height:40px;display:flex;align-items:center}
.brand{display:flex;align-items:center;gap:12px;color:var(--white);font-weight:700;font-size:21px}
.brand-mark{width:40px;height:40px;background:#f0d9a8;border-radius:4px}
.nav-links{margin-left:auto;display:flex;gap:44px;font-size:13px;color:var(--white)}
.nav-links .active{color:var(--gold)}
.hero-title{position:absolute;left:66px;top:175px;color:var(--white);font-size:58px;line-height:75px;font-weight:300}
.hero-title b{font-weight:700}
.hero-title .accent{color:var(--gold);background:radial-gradient(circle,#0d1e57 60%,transparent 62%)}
.hero-copy{position:absolute;left:68px;top:420px;width:420px;color:var(--white);font-size:13px;line-height:20px}
.btn{display:inline-block;border:2px solid var(--ink);background:var(--white);color:var(--ink);font-size:13px;font-weight:700;padding:13px 24px;box-shadow:-8px 8px 0 var(--teal)}
.hero .btn{position:absolute;left:84px;top:502px}
.hero-photo{position:absolute;left:700px;top:138px;width:434px;height:608px;border-radius:217px 217px 200px 200px;background:var(--white);padding:12px}
.hero-photo div{width:100%;height:100%;border-radius:205px 205px 190px 190px;background:linear-gradient(160deg,#c2476f,#6d2c3a 50%,#1c1a22)}

/* About */
.about-photo{position:absolute;left:68px;top:857px;width:446px;height:417px;background:linear-gradient(135deg,#5a4836,#c69a6e 50%,#3b3f52)}
.about-text{position:absolute;left:666px;top:915px;width:470px}
.eyebrow{font-size:13px;letter-spacing:.5px;color:var(--ink)}
.about-text h2{font-size:33px;font-weight:600;margin:6px 0 20px}
.about-text p{font-size:14.5px;line-height:26px;color:#333}
.about-text .btn{position:absolute;left:16px;top:268px}
.signature{position:absolute;left:188px;top:258px;width:200px;height:60px;background:linear-gradient(90deg,rgba(29,29,43,.06),rgba(29,29,43,.12))}

/* Skills */
.section-title{position:absolute;left:0;width:1200px;text-align:center;font-size:34px;font-weight:600}
.skills{position:absolute;top:1420px;left:68px;display:flex;gap:39px}
.skill-card{width:329px;height:399px;background:var(--white);border-radius:16px;box-shadow:0 6px 22px rgba(40,20,90,.14);padding:28px 30px}
.skill-card.featured{background:linear-gradient(180deg,var(--purple-bright),var(--purple));color:var(--white)}
.skill-card li{font-size:14px;height:45.5px;line-height:45.5px;border-bottom:1px solid #e4e4ea}
.skill-card.featured li{border-bottom-color:rgba(255,255,255,.22)}
.skill-card li:last-child{border-bottom:none}
.skill-card li::before{content:"";display:inline-block;width:4px;height:4px;border-radius:50%;background:var(--purple-bright);margin-right:6px;vertical-align:middle}
.skill-card.featured li::before{background:var(--white)}

/* Services */
.services-bg{position:absolute;left:0;top:1920px}
.services-head{position:absolute;top:2036px;left:0;width:1200px;text-align:center;color:var(--white)}
.services-head .eyebrow{color:var(--white)}
.services-head h2{font-size:34px;font-weight:600;margin-top:4px}
.service-card{position:absolute;top:2133px;width:324px;height:436px;color:var(--white)}
.service-card .thumb{height:190px}
.service-card h3{font-size:21px;font-weight:700;margin:40px 0 14px 18px}
.service-card li{font-size:12.5px;font-weight:700;margin-left:18px;height:31px}
.service-card li::before{content:"";display:inline-block;width:5px;height:5px;background:var(--white);margin-right:10px;vertical-align:middle}
.scallop{position:absolute;right:-10px;top:0;width:20px;height:436px}
.slider-arrow{position:absolute;top:2336px}

/* Portfolio */
.portfolio-head{position:absolute;top:2752px;left:0;width:1200px;text-align:center}
.portfolio-head h2{font-size:34px;font-weight:600;margin-top:4px}
.tile{position:absolute;width:346px;height:249px}

/* Pricing */
.pricing-bg{position:absolute;left:0;top:3460px}
.pricing-head{position:absolute;top:3541px;left:0;width:1200px;text-align:center;color:var(--white)}
.pricing-head .eyebrow{color:var(--white)}
.pricing-head h2{font-size:34px;font-weight:600;margin-top:4px}
.package{position:absolute;top:3650px;width:240px;height:340px}
.package svg{position:absolute;left:0;top:0}
.price{position:absolute;left:0;top:72px;width:240px;text-align:center;color:var(--white);font-size:20px;font-weight:800}
.rate{position:absolute;left:28px;top:114px;height:26px;line-height:26px;padding:0 16px;border-radius:13px;background:linear-gradient(90deg,#6a24c0,var(--pink));color:var(--white);font-size:11px;font-weight:700}
.package .box{position:absolute;left:40px;top:152px;width:164px;height:172px;background:var(--white);display:flex;align-items:center;justify-content:center;text-align:center;padding:0 22px;font-size:13px;line-height:23px;color:#333}

/* Testimonials */
.testi-head{position:absolute;top:4155px;left:0;width:1200px;text-align:center}
.testi-head h2{font-size:34px;font-weight:600;margin:4px 0 14px}
.testi-head p{font-size:15.5px;color:#333}
.client-photo{position:absolute;left:534px;top:4309px;width:134px;height:154px;background:linear-gradient(160deg,#7aa25a,#c58a5e 55%,#3e2a22)}
.client-name{position:absolute;top:4484px;left:0;width:1200px;text-align:center;font-size:20px;color:#333}
.client-role{position:absolute;top:4514px;left:0;width:1200px;text-align:center;font-size:13px;color:#555}
.stars{position:absolute;top:4549px;left:528px;display:flex;gap:10px}
.quote{position:absolute;top:4600px;left:248px;width:704px;text-align:center;font-size:16px;line-height:29px;color:#555}
.avatar{position:absolute;border-radius:50%}
.dot{position:absolute;border-radius:50%}
.round-arrow{position:absolute;top:4524px;width:56px;height:56px;border-radius:50%;background:#e8f4f4;display:flex;align-items:center;justify-content:center}

/* Footer */
.footer-bg{position:absolute;left:0;top:4770px}
.footer{position:absolute;left:0;top:4860px;width:1200px;height:436px;color:var(--white)}
.footer .brand{position:absolute;left:68px;top:30px;font-size:15px}
.footer-about{position:absolute;left:68px;top:96px;width:250px;font-size:12px;line-height:22px}
.socials{position:absolute;left:68px;top:172px;display:flex;gap:12px}
.socials span{width:34px;height:34px;border-radius:50%;background:#222}
.socials span:first-child{background:var(--purple-bright)}
.footer-col{position:absolute;top:20px}
.footer-col h4{font-size:14px;font-weight:700;letter-spacing:.5px;margin-bottom:20px}
.footer-col li{font-size:12.5px;height:34px}
.contact-item{display:flex;gap:10px;align-items:flex-start;font-size:12.5px;line-height:18px;margin-bottom:22px}
.contact-item .ico{flex:none;width:34px;height:34px;border:2px solid var(--white);border-radius:50%;display:flex;align-items:center;justify-content:center}
.contact-item span{padding-top:8px}
.copyright{position:absolute;top:356px;left:0;width:1200px;text-align:center;font-size:11.5px;letter-spacing:.3px}
.copyright em{font-style:normal;color:var(--purple-bright)}
</style>
</head>
<body>

<!-- Hero -->
<header class="hero">
  <svg class="hero-wave" width="1200" height="740" viewBox="0 0 1200 740">
    <path d="M0 590 C180 520 380 600 560 640 C760 685 900 560 1200 420 L1200 740 L0 740Z" fill="var(--lavender)"/>
    <path d="M0 640 C180 600 360 680 560 700 C780 720 920 620 1200 520 L1200 740 L0 740Z" fill="var(--white)"/>
  </svg>
  <nav class="nav">
    <div class="brand"><span class="brand-mark"></span>Lena Morvath</div>
    <ul class="nav-links">
      <li class="active">HOME</li><li>ABOUT LENA</li><li>SERVICES</li><li>PORTFOLIO</li><li>PRICING</li><li>CONTACT US</li>
    </ul>
  </nav>
  <h1 class="hero-title">Better<br><b>Commu<span class="accent">nica</span>tion</b><br>For Marketing</h1>
  <p class="hero-copy">Sed ut perspiciatis unde omnis iste natus error sit voluptatem accusantiugs doloremque laudantium</p>
  <a class="btn">READ MORE</a>
  <div class="hero-photo"><div role="img" aria-label="Portrait of Lena smiling in front of pink flowers"></div></div>
</header>

<!-- About -->
<section>
  <div class="about-photo" role="img" aria-label="Close-up photo of Lena smiling outdoors"></div>
  <div class="about-text">
    <p class="eyebrow">WELCOME TO</p>
    <h2>Online Business Manager</h2>
    <p>Hi! I'm so excited that you have chosen to explore my portfolio. Helping businesses achieve their goals is my passion, and I'm thrilled that with my assistance you will have more time for your own passion project. I thrive while working independently, which means you can be confident when leaving tasks for me.</p>
    <a class="btn">READ MORE</a>
    <div class="signature" role="img" aria-label="Handwritten signature of Lena Morvath"></div>
  </div>
</section>

<!-- Skills -->
<section>
  <h2 class="section-title" style="top:1348px">What Our Skills</h2>
  <div class="skills">
    <ul class="skill-card">
      <li>Office Suite</li><li>Design Canvas</li><li>Social Pages</li><li>Task Tracker</li><li>Social Scheduler</li><li>LedgerBooks</li><li>Mail Campaigns</li><li>Web Calls</li>
    </ul>
    <ul class="skill-card featured">
      <li>Cloud Workspace</li><li>Basic Photo Editing</li><li>Photo Social</li><li>Kanban Boards</li><li>Post Planner</li><li>InvoiceBooks</li><li>A/P &amp; A/R</li><li>Note Vault</li>
    </ul>
    <ul class="skill-card">
      <li>Video Calls</li><li>PeoplePrism HR</li><li>Audio Editing</li><li>Transcript Studio</li><li>Contact CRM</li><li>Tide Accounting</li><li>Communication</li><li>Attention to detail</li>
    </ul>
  </div>
</section>

<!-- Services -->
<section>
  <svg class="services-bg" width="1200" height="752" viewBox="0 0 1200 752">
    <path d="M0 12 C160 50 300 64 520 50 C760 34 900 -10 1200 28 L1200 752 L0 752Z" fill="var(--purple)"/>
  </svg>
  <div class="services-head"><p class="eyebrow">SERVICES</p><h2>What We Do</h2></div>

  <article class="service-card" style="left:68px;background:var(--green)">
    <div class="thumb" role="img" aria-label="Laptop keyboard on a light desk" style="background:linear-gradient(135deg,#9aa0a6,#e6e8ea)"></div>
    <h3>Virtual Assistance</h3>
    <ul><li>Calendar Management</li><li>Email Management</li><li>Light Graphic Design</li><li>Data Entry</li></ul>
    <svg class="scallop" viewBox="0 0 20 436"><g fill="var(--purple)">
      <circle cx="20" cy="30" r="8"/><circle cx="20" cy="70" r="8"/><circle cx="20" cy="110" r="8"/><circle cx="20" cy="150" r="8"/><circle cx="20" cy="190" r="8"/><circle cx="20" cy="230" r="8"/><circle cx="20" cy="270" r="8"/><circle cx="20" cy="310" r="8"/><circle cx="20" cy="350" r="8"/><circle cx="20" cy="390" r="8"/></g></svg>
  </article>
  <article class="service-card" style="left:432px;background:var(--green-teal)">
    <div class="thumb" role="img" aria-label="Calculator and paperwork on a blue desk" style="background:linear-gradient(135deg,#9fd3e6,#e9f2f5)"></div>
    <h3>Finance Management</h3>
    <ul><li>Create Invoices</li><li>Track Receivables</li><li>Analyze Expenses</li><li>Year Over Year Analytics</li></ul>
    <svg class="scallop" viewBox="0 0 20 436"><g fill="var(--purple)">
      <circle cx="20" cy="30" r="8"/><circle cx="20" cy="70" r="8"/><circle cx="20" cy="110" r="8"/><circle cx="20" cy="150" r="8"/><circle cx="20" cy="190" r="8"/><circle cx="20" cy="230" r="8"/><circle cx="20" cy="270" r="8"/><circle cx="20" cy="310" r="8"/><circle cx="20" cy="350" r="8"/><circle cx="20" cy="390" r="8"/></g></svg>
  </article>
  <article class="service-card" style="left:795px;background:var(--teal-dark)">
    <div class="thumb" role="img" aria-label="Woman at a desk in front of a wall of sticky notes" style="background:linear-gradient(135deg,#e8a0b8,#eef0f2 50%,#5a5f66)"></div>
    <h3>Business Management</h3>
    <ul><li>Creation of Operating Procedures</li><li>Review of Website Strategy</li><li>Reporting and Analytics</li><li>Project Management</li></ul>
    <svg class="scallop" viewBox="0 0 20 436"><g fill="var(--purple)">
      <circle cx="20" cy="30" r="8"/><circle cx="20" cy="70" r="8"/><circle cx="20" cy="110" r="8"/><circle cx="20" cy="150" r="8"/><circle cx="20" cy="190" r="8"/><circle cx="20" cy="230" r="8"/><circle cx="20" cy="270" r="8"/><circle cx="20" cy="310" r="8"/><circle cx="20" cy="350" r="8"/><circle cx="20" cy="390" r="8"/></g></svg>
  </article>

  <svg class="slider-arrow" style="left:22px" width="24" height="40" viewBox="0 0 24 40"><path d="M20 2 L4 20 L20 38" fill="none" stroke="#b9a6e0" stroke-width="2"/></svg>
  <svg class="slider-arrow" style="left:1156px" width="24" height="40" viewBox="0 0 24 40"><path d="M4 2 L20 20 L4 38" fill="none" stroke="#b9a6e0" stroke-width="2"/></svg>
</section>

<!-- Portfolio -->
<section>
  <div class="portfolio-head"><p class="eyebrow">WORK</p><h2>My Portfolio</h2></div>
  <div class="tile" style="left:68px;top:2852px;background:linear-gradient(135deg,#f2f2f2,#d6d6d6)" role="img" aria-label="Sketched creative process notes beside a coffee cup"></div>
  <div class="tile" style="left:427px;top:2852px;background:linear-gradient(135deg,#4d2a9a,#3a1a80)" role="img" aria-label="Desk workspace under a purple overlay"></div>
  <div class="tile" style="left:787px;top:2852px;background:linear-gradient(135deg,#2b2b2b,#4a4a4a 60%,#b52020)" role="img" aria-label="Keyboard, red mug and swatches on a dark desk"></div>
  <div class="tile" style="left:68px;top:3113px;background:linear-gradient(135deg,#6c6272,#a57a6a 50%,#4a4252)" role="img" aria-label="Coloured pencils in a mug"></div>
  <div class="tile" style="left:427px;top:3113px;background:linear-gradient(135deg,#e8e8e8,#a8532a 55%,#d9d9d9)" role="img" aria-label="Hands opening a brown leather bag"></div>
  <div class="tile" style="left:787px;top:3113px;background:linear-gradient(135deg,#e6e6e6,#c0905e 55%,#eeeeee)" role="img" aria-label="Travel notebook with photos and a toy plane"></div>
</section>

<!-- Pricing -->
<section>
  <svg class="pricing-bg" width="1200" height="620" viewBox="0 0 1200 620">
    <defs><linearGradient id="pricingGrad" x1="0" y1="0" x2="0" y2="1"><stop offset="0" stop-color="#4a1a8e"/><stop offset="1" stop-color="#3a1aa0"/></linearGradient></defs>
    <path d="M0 0 L1200 0 L1200 580 C900 620 700 560 450 575 C250 585 120 600 0 570Z" fill="url(#pricingGrad)"/>
  </svg>
  <div class="pricing-head"><p class="eyebrow">OUR PRICING</p><h2>Rated &amp; Packages</h2></div>

  <div class="package" style="left:79px">
    <svg width="240" height="340" viewBox="0 0 240 340">
      <path d="M14 150 L120 106 L226 150 L226 330 L14 330Z" fill="var(--purple-deep)"/>
      <polygon points="120,44 166,70 166,122 120,148 74,122 74,70" fill="var(--purple-deep)" stroke="var(--purple-bright)" stroke-width="6"/>
    </svg>
    <div class="price">$40</div><div class="rate">HOURLY RATE</div>
    <div class="box">For clients needing only occasional help</div>
  </div>
  <div class="package" style="left:350px">
    <svg width="240" height="340" viewBox="0 0 240 340">
      <path d="M14 150 L120 106 L226 150 L226 330 L14 330Z" fill="var(--purple-deep)"/>
      <polygon points="120,44 166,70 166,122 120,148 74,122 74,70" fill="var(--purple-deep)" stroke="var(--purple-bright)" stroke-width="6"/>
    </svg>
    <div class="price">$700</div><div class="rate">20 HOURS/MONTH</div>
    <div class="box">Includes one 15 minute meeting per week</div>
  </div>
  <div class="package" style="left:618px">
    <svg width="240" height="340" viewBox="0 0 240 340">
      <path d="M14 150 L120 106 L226 150 L226 330 L14 330Z" fill="var(--purple-deep)"/>
      <polygon points="120,44 166,70 166,122 120,148 74,122 74,70" fill="var(--purple-deep)" stroke="var(--purple-bright)" stroke-width="6"/>
    </svg>
    <div class="price">$1,300</div><div class="rate">40 HOURS/MONTH</div>
    <div class="box">Includes one 30 minute meeting per week</div>
  </div>
  <div class="package" style="left:885px">
    <svg width="240" height="340" viewBox="0 0 240 340">
      <path d="M14 150 L120 106 L226 150 L226 330 L14 330Z" fill="var(--purple-deep)"/>
      <polygon points="120,44 166,70 166,122 120,148 74,122 74,70" fill="var(--purple-deep)" stroke="var(--purple-bright)" stroke-width="6"/>
    </svg>
    <div class="price">$2,400</div><div class="rate">80 HOURS/MONTH</div>
    <div class="box">Includes one 60 minute meeting per week</div>
  </div>
</section>

<!-- Testimonials -->
<section>
  <div class="testi-head">
    <p class="eyebrow">TESTIMONIALS</p>
    <h2>What Our Client Says</h2>
    <p>Sed ut perspiciatis unde omnis iste natus error sit voluptatem&nbsp; accusantium</p>
  </div>
  <svg class="abs" style="left:356px;top:4420px" width="480" height="80" viewBox="0 0 480 80">
    <path d="M4 74 C80 30 200 40 260 50 C330 60 400 40 476 30" fill="none" stroke="var(--teal)" stroke-width="3"/>
  </svg>
  <div class="client-photo" role="img" aria-label="Photo of client Dana R. Pellow"></div>
  <p class="client-name">Dana R. Pellow</p>
  <p class="client-role">Ridgeline Renovations</p>
  <div class="stars">
    <svg width="18" height="18" viewBox="0 0 20 20"><polygon points="10,1 12.6,7 19,7.4 14,11.6 15.6,18 10,14.5 4.4,18 6,11.6 1,7.4 7.4,7" fill="var(--gold)"/></svg>
    <svg width="18" height="18" viewBox="0 0 20 20"><polygon points="10,1 12.6,7 19,7.4 14,11.6 15.6,18 10,14.5 4.4,18 6,11.6 1,7.4 7.4,7" fill="var(--gold)"/></svg>
    <svg width="18" height="18" viewBox="0 0 20 20"><polygon points="10,1 12.6,7 19,7.4 14,11.6 15.6,18 10,14.5 4.4,18 6,11.6 1,7.4 7.4,7" fill="var(--gold)"/></svg>
    <svg width="18" height="18" viewBox="0 0 20 20"><polygon points="10,1 12.6,7 19,7.4 14,11.6 15.6,18 10,14.5 4.4,18 6,11.6 1,7.4 7.4,7" fill="var(--gold)"/></svg>
    <svg width="18" height="18" viewBox="0 0 20 20"><polygon points="10,1 12.6,7 19,7.4 14,11.6 15.6,18 10,14.5 4.4,18 6,11.6 1,7.4 7.4,7" fill="var(--gold)"/></svg>
  </div>
  <p class="quote">When it became apparent that a project would take more time than I had, Lena stepped up to take on the required research. She was thorough and timely; able to meet a last-minute 12-hour deadline. I would highly recommend Lena to assist with your next project.</p>

  <div class="avatar" style="left:68px;top:4385px;width:74px;height:74px;background:linear-gradient(160deg,#a3b3a0,#4a3a30)" role="img" aria-label="Client avatar"></div>
  <div class="avatar" style="left:1080px;top:4240px;width:54px;height:54px;background:linear-gradient(160deg,#e0c2a8,#8a6a52)" role="img" aria-label="Client avatar"></div>
  <span class="dot" style="left:143px;top:4310px;width:7px;height:7px;background:#2fd7b6"></span>
  <span class="dot" style="left:1043px;top:4368px;width:12px;height:12px;background:#f5a21a"></span>
  <span class="dot" style="left:384px;top:4513px;width:12px;height:12px;background:#ec4a1e"></span>
  <span class="dot" style="left:901px;top:4496px;width:6px;height:6px;background:var(--purple-bright)"></span>
  <span class="dot" style="left:280px;top:4743px;width:6px;height:6px;background:#3a7be0"></span>

  <div class="round-arrow" style="left:67px">
    <svg width="36" height="16" viewBox="0 0 36 16"><path d="M34 8 H3 M10 1 L2 8 L10 15" fill="none" stroke="var(--ink)" stroke-width="2.4"/></svg>
  </div>
  <div class="round-arrow" style="left:1077px">
    <svg width="36" height="16" viewBox="0 0 36 16"><path d="M2 8 H33 M26 1 L34 8 L26 15" fill="none" stroke="var(--ink)" stroke-width="2.4"/></svg>
  </div>
</section>

<!-- Footer -->
<svg class="footer-bg" width="1200" height="526" viewBox="0 0 1200 526">
  <path d="M0 40 C200 10 420 20 600 50 C800 82 1000 60 1200 40 L1200 526 L0 526Z" fill="var(--black)"/>
</svg>
<footer class="footer">
  <div class="brand"><span class="brand-mark"></span>Lena Morvath</div>
  <p class="footer-about">Sed ut perspiciatis unde omnis iste natus error sit voluptatem...</p>
  <div class="socials"><span></span><span></span><span></span></div>

  <div class="footer-col" style="left:425px">
    <h4>QUICK LINKS</h4>
    <ul><li>Home</li><li>About Lena</li><li>Services</li><li>Portfolio</li><li>Pricing</li><li>Contact Us</li></ul>
  </div>
  <div class="footer-col" style="left:637px">
    <h4>SERVICES</h4>
    <ul><li>Corporate Solution</li><li>Call Center Solution</li><li>Cloud System Solution</li></ul>
  </div>
  <div class="footer-col" style="left:871px;width:270px">
    <h4>CONTACT US</h4>
    <div class="contact-item">
      <div class="ico"><svg width="14" height="16" viewBox="0 0 14 16"><path d="M7 1 C3.7 1 1.5 3.4 1.5 6.3 C1.5 10 7 15 7 15 C7 15 12.5 10 12.5 6.3 C12.5 3.4 10.3 1 7 1Z" fill="var(--purple-bright)"/><circle cx="7" cy="6.3" r="2" fill="var(--white)"/></svg></div>
      <span style="padding-top:0">22 Harbor Lane, Suite 4<br>Brookvale 25kl USA</span>
    </div>
    <div class="contact-item">
      <div class="ico"><svg width="14" height="14" viewBox="0 0 14 14"><path d="M3 1 L5.5 1 L6.5 4 L5 5.2 C5.8 7 7 8.2 8.8 9 L10 7.5 L13 8.5 L13 11 C13 12 12 13 11 13 C5.5 13 1 8.5 1 3 C1 2 2 1 3 1Z" fill="var(--purple-bright)"/></svg></div>
      <span>555.014.2290</span>
    </div>
    <div class="contact-item">
      <div class="ico"><svg width="16" height="12" viewBox="0 0 16 12"><rect x="1" y="1" width="14" height="10" rx="1.5" fill="var(--purple-bright)"/><path d="M1.5 2 L8 7 L14.5 2" fill="none" stroke="var(--white)" stroke-width="1.2"/></svg></div>
      <span>lena.morvath@mailbox.test</span>
    </div>
  </div>

  <p class="copyright">COPYRIGHT © 2023 <em>LENA MORVATH</em> . ALL RIGHTS RESERVED.</p>
</footer>

</body>
</html>
```